High-end construction company needs a business card design

We need a modern looking business card that draws people in, is memorable and looks so good people will want to sick it on their fridges.
On the first side what is needed are:
Logo
My name - Tomasz Brelwik
Title - Managing Director
Website - www.varkelt.co.uk
Email - tomasz@varkelt.co.uk
Telephone - 020 5194 6281
Mobile - 07845139072
On the back side was is needed is a list of all the services we provide:
-Kitchen Renovations
-Bathroom Renovations
-House Renovations
-Garage Conversions
-Extensions
-Loft Conversions
-Conservatories
-Carpentry
-Tiling
-Electrical
-Plumbing & Heating
-Bricklaying
-Landscaping
-Decorating
-Plastering
We would like the colours to be the same shades as on the logo with grey or black for the words.
Target Market(s)
Anyone who needs building work done
Contact Information for Business Card
This business card is for a construction company which strives to deliver excellent service and quality.
The look and feel of the card should represent this.
Requirements
Must have
- On the first side what is needed are:
Logo
My name - Tomasz Brelwik
Title - Managing Director
Website - www.varkelt.co.uk
Email - tomasz@varkelt.co.uk
Telephone - 020 5194 6281
Mobile - 07845139072
Nice to have
- Cool looking features

```html
<!DOCTYPE html>
<html lang="en">
<head>
<meta charset="utf-8">
<title>Varkelt Construction Ltd – Business Card</title>
<link rel="stylesheet" href="https://fonts.googleapis.com/css2?family=Montserrat:wght@400;600;700&display=swap">
<style>
  :root {
    --page-bg: #3a3431;
    --card-bg: #121212;
    --card-edge: #3d9a2a;
    --brand-green: #5cc93a;
    --text-light: #f2f2f2;
  }
  * { box-sizing: border-box; margin: 0; padding: 0; }
  html, body { width: 1200px; height: 716px; overflow: hidden; }
  body {
    background: var(--page-bg);
    font-family: "Montserrat", Arial, sans-serif;
    position: relative;
  }
  .card {
    position: absolute;
    top: 204px;
    width: 540px;
    height: 308px;
    background: var(--card-bg);
    border-radius: 8px;
    box-shadow: 0 10px 30px rgba(0,0,0,.45);
    overflow: hidden;
  }
  .card--back { left: 40px; border-bottom: 4px solid var(--card-edge); }
  .card--front { left: 620px; }

  /* Back: services */
  .services {
    position: absolute;
    left: 40px;
    top: 30px;
    list-style: none;
  }
  .services li {
    color: var(--text-light);
    font-size: 11.5px;
    line-height: 16.3px;
    padding-left: 16px;
    position: relative;
  }
  .services li::before {
    content: "";
    position: absolute;
    left: 0;
    top: 5px;
    width: 6px;
    height: 6px;
    border-radius: 50%;
    background: var(--brand-green);
  }

  /* Wordmark */
  .wordmark {
    position: absolute;
    display: flex;
    align-items: center;
    gap: 10px;
    white-space: nowrap;
  }
  .wordmark__square {
    width: 18px;
    height: 18px;
    background: var(--brand-green);
    flex: none;
  }
  .wordmark__name {
    color: var(--brand-green);
    font-weight: 700;
    font-size: 18px;
    line-height: 23px;
    letter-spacing: .5px;
  }
  .card--back .wordmark { left: 250px; top: 140px; }
  .card--front .wordmark { left: 32px; top: 120px; }

  /* Front: contact */
  .divider {
    position: absolute;
    left: 300px;
    top: 58px;
    width: 2px;
    height: 192px;
    background: var(--brand-green);
  }
  .contact {
    position: absolute;
    left: 326px;
    top: 74px;
    color: var(--text-light);
  }
  .contact__name {
    color: var(--brand-green);
    font-weight: 600;
    font-size: 17px;
    margin-bottom: 2px;
  }
  .contact__title { font-size: 12px; margin-bottom: 10px; }
  .contact__address { font-size: 12px; line-height: 17px; margin-bottom: 8px; font-style: normal; }
  .contact__row {
    display: flex;
    align-items: center;
    gap: 7px;
    font-size: 12px;
    line-height: 18px;
  }
  .contact__row svg { width: 10px; height: 10px; flex: none; }
</style>
</head>
<body>

  <section class="card card--back" aria-label="Business card, services side">
    <ul class="services">
      <li>Kitchen Renovations</li>
      <li>Bathroom Renovations</li>
      <li>House Renovations</li>
      <li>Garage Conversions</li>
      <li>Extensions</li>
      <li>Loft Conversions</li>
      <li>Conservatories</li>
      <li>Carpentry</li>
      <li>Tiling</li>
      <li>Electrical</li>
      <li>Plumbing &amp; Heating</li>
      <li>Bricklaying</li>
      <li>Landscaping</li>
      <li>Decorating</li>
      <li>Plastering</li>
    </ul>
    <div class="wordmark">
      <span class="wordmark__square"></span>
      <span class="wordmark__name">VARKELT<br>CONSTRUCTION LTD</span>
    </div>
  </section>

  <section class="card card--front" aria-label="Business card, contact side">
    <div class="wordmark">
      <span class="wordmark__square"></span>
      <span class="wordmark__name">VARKELT<br>CONSTRUCTION LTD</span>
    </div>
    <div class="divider"></div>
    <div class="contact">
      <p class="contact__name">Tomasz Brelwik</p>
      <p class="contact__title">Managing Director</p>
      <address class="contact__address">14-16 Harrow Lane,<br>London, E2 8QT</address>
      <p class="contact__row">
        <svg viewBox="0 0 10 10" aria-hidden="true"><path d="M2 1l2 2-1 1.2c.6 1.2 1.5 2.1 2.8 2.8L7 6l2 2-1.3 1.5C4.5 9.2.8 5.5.5 2.3z" fill="#5cc93a"/></svg>
        020 5194 6281
      </p>
      <p class="contact__row">
        <svg viewBox="0 0 10 10" aria-hidden="true"><rect x="2.5" y=".5" width="5" height="9" rx="1" fill="none" stroke="#5cc93a"/><circle cx="5" cy="8" r=".6" fill="#5cc93a"/></svg>
        07845139072
      </p>
      <p class="contact__row">
        <svg viewBox="0 0 10 10" aria-hidden="true"><rect x=".5" y="2" width="9" height="6" fill="none" stroke="#5cc93a"/><path d="M.5 2L5 5.5 9.5 2" fill="none" stroke="#5cc93a"/></svg>
        tomasz@varkelt.co.uk
      </p>
      <p class="contact__row">
        <svg viewBox="0 0 10 10" aria-hidden="true"><circle cx="5" cy="5" r="4.5" fill="none" stroke="#5cc93a"/><ellipse cx="5" cy="5" rx="2" ry="4.5" fill="none" stroke="#5cc93a"/><path d="M.5 5h9" stroke="#5cc93a"/></svg>
        www.varkelt.co.uk
      </p>
    </div>
  </section>

</body>
</html>
```